Awesome Business Card Design needed!

Hey there.
I'm looking for a simple but awesome business card design.
Type of company: Online advertisement agency
(please don't use the typical business people or statistics images on the card)
The front has to display the business name
and possibly some sort of logo ( perhaps something with the two M's of the biz name )
And the back of the card should say:
Name
Phone
Email
Let your imagination flow.
here are some designs that I like and that you can use as inspiration.
Simple but Awesome
http://images.lumavexo.com/designs/55128_877673_43091_thumbnail.jpg
http://images.lumavexo.com/designs/37714_747642_40106_image.jpg
http://images.lumavexo.com/designs/55128_877673_43091_image.jpg
http://images.lumavexo.com/designs/51321_781878_43091_image.jpg
http://images.lumavexo.com/designs/33378_399063_15912_image.jpg
http://images.lumavexo.com/designs/2337_271604_9495_image.jpg
good luck

```html
<!DOCTYPE html>
<html lang="en">
<head>
<meta charset="utf-8">
<title>Veldora Media – Business Card</title>
<link rel="stylesheet" href="https://fonts.googleapis.com/css2?family=Jost:wght@400&family=Questrial&display=swap">
<style>
  :root {
    --canvas-bg: #f1f1f1;
    --card-black: #151515;
    --card-white: #f2f0ea;
    --ink-white: #ffffff;
    --ink-black: #141414;
    --pattern-light: #e4e2dc;
    --pattern-dark: #b9b7b2;
    --card-shadow: rgba(0, 0, 0, 0.18);
  }
  * { box-sizing: border-box; margin: 0; padding: 0; }
  html, body {
    width: 1200px;
    height: 1200px;
    overflow: hidden;
    background: var(--canvas-bg);
  }
  .canvas {
    width: 1200px;
    height: 1200px;
    display: flex;
    flex-direction: column;
    align-items: center;
    justify-content: center;
    gap: 60px;
  }
  .card {
    position: relative;
    width: 700px;
    height: 400px;
    box-shadow: 0 12px 30px var(--card-shadow);
    overflow: hidden;
  }
  .card--front {
    background: var(--card-black);
    display: flex;
    align-items: center;
    justify-content: center;
  }
  .brand-name {
    font-family: "Jost", sans-serif;
    font-weight: 400;
    font-size: 62px;
    letter-spacing: 1px;
    color: var(--ink-white);
    white-space: nowrap;
  }
  .card--back {
    background: var(--card-white);
  }
  .contact {
    position: absolute;
    left: 62px;
    top: 40px;
    font-family: "Questrial", sans-serif;
    font-weight: 400;
    font-size: 35px;
    line-height: 36px;
    color: var(--ink-black);
    list-style: none;
    white-space: nowrap;
    z-index: 1;
  }
  .contact__name { padding-left: 4px; }
  .line-pattern {
    position: absolute;
    right: 0;
    bottom: 0;
    width: 480px;
    height: 400px;
    background: radial-gradient(ellipse at 100% 100%,
      var(--pattern-dark) 0%,
      var(--pattern-light) 45%,
      var(--card-white) 72%);
  }
</style>
</head>
<body>
  <main class="canvas">
    <section class="card card--front" aria-label="Card front">
      <h1 class="brand-name">VELDORA MEDIA</h1>
    </section>

    <section class="card card--back" aria-label="Card back">
      <div class="line-pattern" role="img" aria-label="Decorative fan of sweeping black curved lines"></div>
      <ul class="contact">
        <li class="contact__name">marketer name</li>
        <li class="contact__phone">000 000 0000</li>
        <li class="contact__email">name@veldoramedia.com</li>
      </ul>
    </section>
  </main>
</body>
</html>
```